Business Card Design (NEW FILES)

ATTENTION: New vector files are available. Please update your design to reflect/use the new (better resolution) logo images.

Seeking a unique and professional business card design for a commercial drone photography/videography business. The layout should feature
the logo (attached) and include the following information:
Owen Tarrick
614-502-7738
www.skylarkreelworks.example
NRD Certified Remote Pilot

Owen Tarrick

```html
<!DOCTYPE html>
<html lang="en">
<head>
<meta charset="utf-8">
<title>Skylark Reelworks – Business Card</title>
<link href="https://fonts.googleapis.com/css2?family=Open+Sans:wght@400;600;700;800&display=swap" rel="stylesheet">
<style>
  :root {
    --backdrop: #232323;
    --card-navy: #161a45;
    --card-navy-deep: #12163d;
    --accent-orange: #e07a35;
    --ink-white: #ffffff;
    --ink-soft: #e6e7f0;
  }
  * { box-sizing: border-box; margin: 0; padding: 0; }
  html, body {
    width: 1200px;
    height: 780px;
    overflow: hidden;
    background: var(--backdrop);
    font-family: "Open Sans", Arial, sans-serif;
  }
  .sheet {
    width: 1200px;
    height: 780px;
    display: flex;
    align-items: center;
    justify-content: center;
    gap: 40px;
  }
  .card {
    position: relative;
    width: 540px;
    height: 310px;
    background: var(--card-navy);
    border-bottom: 4px solid var(--accent-orange);
    overflow: hidden;
  }
  .card--back { background: var(--card-navy-deep); }

  /* Brand name lockup */
  .brand {
    display: flex;
    align-items: center;
    gap: 10px;
    color: var(--ink-white);
    font-weight: 600;
    white-space: nowrap;
  }
  .brand__dot {
    border-radius: 50%;
    background: var(--accent-orange);
    flex: none;
  }
  .card--front .brand {
    position: absolute;
    left: 34px;
    top: 62px;
    font-size: 22px;
  }
  .card--front .brand__dot { width: 14px; height: 14px; }
  .card--back .brand {
    position: absolute;
    left: 50%;
    top: 50%;
    transform: translate(-50%, -50%);
    font-size: 38px;
  }
  .card--back .brand__dot { width: 22px; height: 22px; }

  .credential {
    position: absolute;
    left: 34px;
    bottom: 40px;
    width: 220px;
    color: var(--ink-soft);
    font-size: 13px;
    line-height: 1.5;
  }

  .divider {
    position: absolute;
    left: 268px;
    top: 50px;
    width: 2px;
    height: 210px;
    background: var(--accent-orange);
  }

  .contact {
    position: absolute;
    left: 296px;
    top: 92px;
    width: 230px;
  }
  .contact__name {
    font-size: 24px;
    font-weight: 800;
    color: var(--ink-white);
    line-height: 1.1;
  }
  .contact__first { color: var(--accent-orange); }
  .contact__role {
    font-size: 13px;
    color: var(--ink-soft);
    margin-top: 2px;
    margin-bottom: 16px;
  }
  .contact__list { list-style: none; }
  .contact__item {
    display: flex;
    align-items: center;
    gap: 8px;
    font-size: 12px;
    color: var(--ink-white);
    margin-bottom: 7px;
    white-space: nowrap;
  }
  .contact__icon { width: 13px; height: 13px; flex: none; }
</style>
</head>
<body>
<main class="sheet">
  <section class="card card--front">
    <div class="brand"><span class="brand__dot"></span>Skylark Reelworks</div>
    <p class="credential">NRD Certified Remote Pilot Fully Insured</p>
    <div class="divider"></div>
    <div class="contact">
      <h1 class="contact__name"><span class="contact__first">Owen</span> Tarrick</h1>
      <p class="contact__role">Owner</p>
      <ul class="contact__list">
        <li class="contact__item">
          <svg class="contact__icon" viewBox="0 0 24 24" aria-hidden="true"><path fill="#e07a35" d="M6.6 10.8a15.2 15.2 0 0 0 6.6 6.6l2.2-2.2a1 1 0 0 1 1-.25 11.4 11.4 0 0 0 3.6.57 1 1 0 0 1 1 1V20a1 1 0 0 1-1 1A17 17 0 0 1 3 4a1 1 0 0 1 1-1h3.5a1 1 0 0 1 1 1c0 1.25.2 2.45.57 3.57a1 1 0 0 1-.25 1z"/></svg>
          614-502-7738
        </li>
        <li class="contact__item">
          <svg class="contact__icon" viewBox="0 0 24 24" aria-hidden="true"><circle cx="12" cy="12" r="9" fill="none" stroke="#e07a35" stroke-width="2"/><path d="M3 12h18M12 3c3 3 3 15 0 18M12 3c-3 3-3 15 0 18" fill="none" stroke="#e07a35" stroke-width="1.6"/></svg>
          www.skylarkreelworks.example
        </li>
        <li class="contact__item">
          <svg class="contact__icon" viewBox="0 0 24 24" aria-hidden="true"><rect x="2" y="5" width="20" height="14" rx="2" fill="#e07a35"/><path d="M3 6l9 7 9-7" fill="none" stroke="#161a45" stroke-width="1.8"/></svg>
          info@skylarkreelworks.example
        </li>
      </ul>
    </div>
  </section>

  <section class="card card--back">
    <div class="brand"><span class="brand__dot"></span>Skylark Reelworks</div>
  </section>
</main>
</body>
</html>
```